Lone Star Wetland Flora Stewardship Guild

We need to design the home page of this new website. We would like a fun website design for provides as a resource for members and information for potential members.
Please design so that we can see a portion of background on each side on the website.
I just need the final design files psd no coding needed.
Attached is their logo (colors are not 100% set in stone either so can mess with those as I did in the quick mockup attached)
Attached is a pdf newsletter they send out, you can get a feel for them and what they are about. The design is crappy and we are here to fix that going forward and we are starting with the website.
Here are some quick example websites (design style is open)
- I attached a quick mockup i did just for a content visual but by all means do what you want.
- http://www.brightpathleaders.example/
- http://www.civicunityhub.example/
- http://preview.webskinvault.example/show.php?cat=layouts&host=skinbazaar&temp=novaline
- http://www.meadowkeep.example/
- http://www.urbangleaners.example/
- http://www.projectcozyknit.example/
here are some of the other chapters website (pretty bad!)
and here are some of the others:
- http://www.dwrvcs.example/
- http://kwfg.example/
- http://www.blvcg.example/
Content Items that need to be included:
1. Logo
2. Menu - home, about, members, resources, events, membership, contact
3. Become a member - button or action
4. social links - chatterloop, workweave, clipstream
5. banner - that needs to explain their purpose "Promoting environmental stewardship through operations, research, education and outreach" (or this can be worked into the design)
6. Upcoming event (s)
7. Advertisement - members can place an ad on the website, this can be a placeholder for now
8. newsletter signup
9. advertise with us - this link can be in the footer
30-60 years of age, succesfull (household budgets of 120K+ men and women that live in texas.
Education

```html
<!DOCTYPE html>
<html lang="en">
<head>
<meta charset="utf-8">
<title>Lone Star Wetland Flora Stewardship Guild</title>
<link rel="stylesheet" href="https://fonts.googleapis.com/css2?family=Figtree:wght@400;500&family=Arimo:wght@400;700&display=swap">
<style>
:root{
  --red:#d9485a;
  --navy:#0b3d8c;
  --navy-dark:#083278;
  --text-grey:#8a8a8a;
  --ink:#222;
  --white:#fff;
  --sky-top:#0b2c5c;
  --sky-mid:#8fb4d6;
  --cloud:#eef3f6;
  --grass-light:#b8d24a;
  --grass-dark:#4f7e16;
}
*{box-sizing:border-box;margin:0;padding:0}
html,body{width:1040px;height:1200px;overflow:hidden}
body{position:relative;font-family:"Arimo",Arial,sans-serif;color:var(--ink);background:var(--white)}
a{text-decoration:none;color:inherit}
.backdrop{position:absolute;inset:0;background:linear-gradient(180deg,var(--sky-top) 0%,#245487 10%,var(--sky-mid) 20%,var(--cloud) 34%,#dfe9ec 46%,#6f8f3a 54%,var(--grass-light) 64%,#8fb331 78%,var(--grass-dark) 100%)}
.page{position:absolute;left:114px;top:0;width:812px;height:1066px;background:var(--white)}
.header{position:absolute;left:0;top:0;width:812px;height:114px}
.brand{position:absolute;left:13px;top:30px;display:flex;align-items:center;gap:10px}
.brand-mark{width:26px;height:26px;background:var(--red)}
.brand-name{font-family:"Figtree",sans-serif;font-weight:500;font-size:19px;line-height:22px;color:var(--navy);width:220px}
.signup{position:absolute;left:451px;top:14px;width:350px}
.signup p{font-size:12px;line-height:19.5px;color:var(--navy)}
.signup-form{display:flex;gap:10px;margin-top:18px}
.field{width:104px;height:27px;border:1px solid #9a9a9a;border-radius:2px;font-size:12px;color:#9a9a9a;padding:6px 10px}
.btn-signup{width:104px;height:27px;background:var(--navy);color:var(--white);border-radius:2px;font-size:12px;text-align:center;line-height:27px}
.nav{position:absolute;left:0;top:114px;width:812px;height:68px;background:var(--red);display:flex;align-items:center}
.nav a{font-size:13px;font-weight:700;color:var(--white);text-transform:uppercase;height:68px;line-height:68px}
.nav .active{background:var(--navy);padding:0 13px}
.hero{position:absolute;left:13.5px;top:193px;width:783px;height:307px;background:linear-gradient(180deg,#cfe2f1 0%,#eaf1f6 18%,#7aa443 32%,#3f7a22 52%,#556b3a 70%,#3b4a2a 100%)}
.hero-caption{position:absolute;left:0;bottom:0;width:783px;height:86px;background:rgba(20,20,20,.82);color:var(--white);font-family:"Figtree",sans-serif;font-size:26px;line-height:32px;padding:14px 22px}
.hero-arrows{position:absolute;right:24px;top:30px;display:flex;gap:14px}
.welcome-title{position:absolute;left:14px;top:518px;font-family:"Figtree",sans-serif;font-size:28px;font-weight:400;color:var(--red)}
.welcome-title span,.section-title span{color:var(--navy)}
.welcome-text{position:absolute;left:14px;top:560px;width:780px;font-size:12.5px;line-height:19.5px;color:var(--text-grey)}
.btn-member{position:absolute;left:13.5px;top:631px;width:238px;height:51px;background:var(--navy);border-radius:2px;color:var(--white);font-family:"Figtree",sans-serif;font-size:19px;display:flex;align-items:center;gap:12px;padding-left:22px}
.section-title{position:absolute;left:16px;top:700px;font-family:"Figtree",sans-serif;font-size:28px;font-weight:400;color:var(--red)}
.events-arrows{position:absolute;left:491px;top:709px;display:flex;gap:6px}
.events-arrows span{width:24px;height:19px;background:var(--navy);display:flex;align-items:center;justify-content:center}
.event{position:absolute;top:754px;width:255px}
.event-photo{width:255px;height:172px;border:1px solid #ddd;padding:4px}
.event-photo div{position:relative;width:100%;height:100%}
.event-date{position:absolute;right:0;bottom:0;background:rgba(20,20,20,.8);color:var(--white);font-family:"Figtree",sans-serif;font-size:19px;padding:6px 13px}
.event h3{font-family:"Figtree",sans-serif;font-weight:400;font-size:19px;margin-top:10px}
.event p{font-size:12.5px;line-height:19.5px;color:var(--text-grey);margin-top:6px}
.event .more{font-size:12.5px;color:var(--navy)}
.ad{position:absolute;left:563px;top:710px;width:233px;height:327px;background:linear-gradient(180deg,#3f8fc9 0%,#1d3c6c 40%,#151822 75%,#d4d4d6 79%,#e1e1e3 100%)}
.footer{position:absolute;left:0;top:1066px;width:1040px;height:134px;background:rgba(255,255,255,.82)}
.footer-links{position:absolute;left:127px;top:38px;display:flex;gap:14px;font-size:12.5px;color:var(--navy)}
.copyright{position:absolute;left:128px;top:79px;font-size:12.5px;color:var(--navy)}
.advertise{position:absolute;left:806px;top:38px;font-size:12.5px;color:var(--navy)}
.social{position:absolute;left:804px;top:66px;display:flex;gap:12px}
.social a{width:24px;height:24px}
.chatterloop{background:#3b5b9a}.workweave{background:#1a7ab5}.clipstream{background:#e4553b}
</style>
</head>
<body>
<div class="backdrop" role="img" aria-label="Blue sky with clouds over a green wheat field"></div>
<div class="page">
  <header class="header">
    <a class="brand" href="#"><span class="brand-mark"></span><span class="brand-name">Lone Star Wetland Flora Stewardship Guild</span></a>
    <div class="signup">
      <p>Lorem ipsum dolor sit amet, tale vocent saperet eu eos, ne eum dissentiunt efficiantur voluptatibus,</p>
      <div class="signup-form"><span class="field">Name</span><span class="field">Email</span><span class="btn-signup">Sign Up</span></div>
    </div>
  </header>
  <nav class="nav">
    <a class="active" href="#">Home</a>
    <a href="#" style="margin-left:46px">About</a>
    <a href="#" style="margin-left:67px">Members</a>
    <a href="#" style="margin-left:60px">Resources</a>
    <a href="#" style="margin-left:56px">Events</a>
    <a href="#" style="margin-left:60px">Membership</a>
    <a href="#" style="margin-left:56px">Contact</a>
  </nav>
  <section class="hero" role="img" aria-label="Photo of a calm pond with water lilies and green trees under a bright sky">
    <div class="hero-caption">Promoting environmental stewardship through<br>operations, research, education and outreach.
      <div class="hero-arrows">
        <svg width="16" height="28" viewBox="0 0 16 28"><path d="M14 2 2 14l12 12" fill="none" stroke="#fff" stroke-width="2.5"/></svg>
        <svg width="16" height="28" viewBox="0 0 16 28"><path d="M2 2l12 12L2 26" fill="none" stroke="#fff" stroke-width="2.5"/></svg>
      </div>
    </div>
  </section>
  <h1 class="welcome-title">Welcome to <span>LSWFSG</span></h1>
  <p class="welcome-text">Lorem ipsum dolor sit amet, tale vocent saperet eu eos, ne eum dissentiunt efficiantur voluptatibus, mea ea suas civibus. Ut quem utroque sit, recteque pertinacia ne mei. Diam homero possim in nam, elit possim ius et. Veri scriptorem vis ea.Lorem ipsum dolor sit amet, tale vocent saperet eu eos, ne eum dissentiunt efficiantur voluptatibus, mea ea suas civibus.</p>
  <a class="btn-member" href="#">
    <svg width="18" height="22" viewBox="0 0 18 22"><circle cx="9" cy="6" r="5" fill="#fff"/><path d="M0 22c0-6 4-9 9-9s9 3 9 9z" fill="#fff"/></svg>
    Become a Member</a>
  <h2 class="section-title">Upcoming <span>Events</span></h2>
  <div class="events-arrows">
    <span><svg width="8" height="12" viewBox="0 0 8 12"><path d="M6 1 1 6l5 5" fill="none" stroke="#fff" stroke-width="2"/></svg></span>
    <span><svg width="8" height="12" viewBox="0 0 8 12"><path d="M2 1l5 5-5 5" fill="none" stroke="#fff" stroke-width="2"/></svg></span>
  </div>
  <article class="event" style="left:13.5px">
    <div class="event-photo"><div role="img" aria-label="Photo of tall reeds growing at the edge of a still pond" style="background:linear-gradient(180deg,#e9eef0 0%,#9fbe5a 25%,#4f8a2a 55%,#7c9a86 80%,#a9b7b4 100%)"><span class="event-date">Aug 12, 2014</span></div></div>
    <h3>Mel ne eirmod</h3>
    <p>Usu et veri persecuti. Veri tollit ignota ius an, te vitae antiopam petentium vix, simul minimum expetendis mea ea.</p>
    <a class="more" href="#">Read More...</a>
  </article>
  <article class="event" style="left:288px">
    <div class="event-photo"><div role="img" aria-label="Photo of lily pads and reeds on dark water" style="background:linear-gradient(180deg,#5f7f7c 0%,#3f6152 40%,#5c8a3e 70%,#3d5a3a 100%)"><span class="event-date">Aug 31, 2014</span></div></div>
    <h3>Mel ne eirmod</h3>
    <p>Usu et veri persecuti. Veri tollit ignota ius an, te vitae antiopam petentium vix, simul minimum expetendis mea ea.</p>
    <a class="more" href="#">Read More...</a>
  </article>
  <aside class="ad" role="img" aria-label="Member advertisement placeholder showing water treatment product packaging"></aside>
</div>
<footer class="footer">
  <nav class="footer-links">
    <a href="#">Home</a><span>I</span><a href="#">About</a><span>I</span><a href="#">Members</a><span>I</span><a href="#">Resources</a><span>I</span><a href="#">Events</a><span>I</span><a href="#">Membership</a><span>I</span><a href="#">Contact</a>
  </nav>
  <p class="copyright">Copyright @ 2014 Lswfsg.All Rights Reserved.</p>
  <a class="advertise" href="#">Advertise With Us</a>
  <div class="social">
    <a class="chatterloop" href="#" aria-label="chatterloop"></a>
    <a class="workweave" href="#" aria-label="workweave"></a>
    <a class="clipstream" href="#" aria-label="clipstream"></a>
  </div>
</footer>
</body>
</html>
```